Brovick Engineering Core Values Branding Package

Brovick Engineering has recently refined its company Core Values and is seeking a strong, cohesive branding package to visually bring these values to life. The new graphic assets will communicate our commitment to excellence in a way that resonates with our team, clients, and partners in a blue-collar, industrial environment.

We are looking for multiple visual assets with consistent design elements that can be applied across platforms. The tone should reflect strength, reliability, and professionalism while remaining approachable and aligned with our industry.

Core Values & Descriptions
Accountability
“We take ownership of our work and actions, ensuring reliability and trust in every solution we deliver.”

Teamwork
“We collaborate across departments and disciplines to provide the highest level of service and innovation for our clients.”

Integrity
“We operate with honesty, transparency, and ethical standards in all aspects of our business.”

Growth
“We are committed to continuous improvement—of our people, our processes, and our impact in the industry.”

Deliverables

1. Primary Core Values Graphic
A master visual representing all four values together.
Designed for use on posters, office signage, internal presentations.

2. Individual Value Graphics (x4)
One graphic per core value: Accountability, Teamwork, Integrity, Growth.
Cohesive style with slight visual variation to reflect each value’s unique meaning.

Target Market(s)

Employees of Brovick Engineering

Industry/Entity Type

Blue Collar

Font styles to use
Sans Serif

Colors
0054AA
0677BA
7BADD7
CADEEF
E8F1F8
00AB8E
00BBA5
67D7C9
C6EFE9
E9F9F6
EB3D1F
EC4F4E
F09395
F8D3D4
FCEDEE

Requirements
Must have
• Accountability, Teamwork, Integrity, Growth

```html
<!DOCTYPE html>
<html lang="en">
<head>
<meta charset="utf-8">
<title>Brovick Engineering – Core Values</title>
<link href="https://fonts.googleapis.com/css2?family=Archivo+Black&family=Oswald:wght@700&family=Arimo:wght@700&display=swap" rel="stylesheet">
<style>
  :root {
    --navy: #00305f;
    --green: #3aaa35;
    --band: #cfd8e2;
    --paper: #ffffff;
    --ink: #111111;
    --url: #7f93b1;
  }
  * { margin: 0; padding: 0; box-sizing: border-box; }
  html, body { width: 731px; height: 1200px; overflow: hidden; background: var(--paper); }
  .poster { position: relative; width: 731px; height: 1200px; background: var(--paper); }

  .side-band { position: absolute; left: 0; top: 0; width: 145px; height: 1200px; background: var(--band); }
  .side-title {
    position: absolute; left: 72px; top: 590px;
    transform: translate(-50%, -50%) rotate(-90deg);
    white-space: nowrap;
    font-family: "Archivo Black", sans-serif;
    font-size: 118px; line-height: 1; letter-spacing: 1px;
    color: var(--navy);
  }

  .brand { position: absolute; left: 198px; top: 118px; display: flex; align-items: center; gap: 14px; }
  .brand-dot { width: 26px; height: 26px; border-radius: 50%; background: var(--green); }
  .brand-name { font-family: "Archivo Black", sans-serif; font-size: 56px; line-height: 1; color: var(--navy); letter-spacing: 1px; }

  .value-icon { position: absolute; left: 166px; width: 114px; height: 114px; }

  .value-text { position: absolute; left: 302px; width: 380px; }
  .value-title {
    font-family: "Oswald", sans-serif; font-weight: 700;
    font-size: 40px; line-height: 1; color: var(--green);
    letter-spacing: -0.5px; margin-bottom: 8px;
  }
  .value-desc { font-family: "Arimo", sans-serif; font-weight: 700; font-size: 16px; line-height: 21px; color: var(--ink); }

  .divider { position: absolute; left: 204px; width: 476px; height: 2px; background: var(--green); }
  .divider::before {
    content: ""; position: absolute; left: -5px; top: -4px;
    width: 10px; height: 10px; border-radius: 50%; background: var(--green);
  }

  .web-address {
    position: absolute; right: 52px; top: 1136px;
    font-family: "Arimo", sans-serif; font-weight: 700;
    font-size: 21px; letter-spacing: 3px; color: var(--url);
  }
</style>
</head>
<body>
<main class="poster">
  <aside class="side-band">
    <h1 class="side-title">CORE VALUES</h1>
  </aside>

  <div class="brand">
    <span class="brand-name">BROVICK</span>
    <span class="brand-dot"></span>
  </div>

  <svg class="value-icon" style="top:323px" viewBox="0 0 114 114" role="img" aria-label="Accountability icon: document review with person and cycle arrows">
    <circle cx="57" cy="57" r="51" fill="#eef2f7" stroke="#3aaa35" stroke-width="8"/>
  </svg>
  <section class="value-text" style="top:310px">
    <h2 class="value-title">ACCOUNTABILITY:</h2>
    <p class="value-desc">We take ownership of our work and actions, ensuring reliability and trust in every solution we deliver.</p>
  </section>

  <div class="divider" style="top:476px"></div>

  <svg class="value-icon" style="top:513px" viewBox="0 0 114 114" role="img" aria-label="Teamwork icon: two hands clasped in a handshake">
    <circle cx="57" cy="57" r="51" fill="#eef2f7" stroke="#3aaa35" stroke-width="8"/>
  </svg>
  <section class="value-text" style="top:500px">
    <h2 class="value-title">TEAMWORK:</h2>
    <p class="value-desc">We collaborate across departments and disciplines to provide the highest level of service and innovation for our clients.</p>
  </section>

  <div class="divider" style="top:672px"></div>

  <svg class="value-icon" style="top:711px" viewBox="0 0 114 114" role="img" aria-label="Integrity icon: gear between two people with circular arrows">
    <circle cx="57" cy="57" r="51" fill="#eef2f7" stroke="#3aaa35" stroke-width="8"/>
  </svg>
  <section class="value-text" style="top:704px">
    <h2 class="value-title">INTEGRITY:</h2>
    <p class="value-desc">We operate with honesty, transparency, and ethical standards in all aspects of our business.</p>
  </section>

  <div class="divider" style="top:876px"></div>

  <svg class="value-icon" style="top:915px" viewBox="0 0 114 114" role="img" aria-label="Growth icon: rising bars with upward arrow">
    <circle cx="57" cy="57" r="51" fill="#eef2f7" stroke="#3aaa35" stroke-width="8"/>
  </svg>
  <section class="value-text" style="top:904px">
    <h2 class="value-title">GROWTH:</h2>
    <p class="value-desc">We are committed to continuous improvement—of our people, our processes, and our impact in the industry.</p>
  </section>

  <p class="web-address">WWW.BROVICK.COM</p>
</main>
</body>
</html>
```